Quill Press Oceania needs a website

We require a website design which will be different to the normal websites that you visit. The objective of this website will be a call to action on the last page which will link to our email address so customers can email us their quotation requirements.

An example of how we envisage the look and the pages turning is as a flip books for example: https://www.vidharbor.example/watch?v=KtLmPzQa7Rw&feature=vh.be

page 1: just has our logo on it with the tag "Specialist producing quality printed books to your deadline."

Page 2: Black Page with white text "Black and White Book"
These are produced either digitally or offset on a complete range of stocks

Page 3: Colour books (use an image of your choice) These are also produced either digitally or offset plus we have the choice of web presses for larger print runs

Page 4: Digital books We do have a minimum run of 50 books using this process so a one off Thesis is not economically viable using this process. In special circumstance the digital process can produce books more quickly then by using our offset printing process.

Page 5: Having the complete range of printing machines at our disposal enables you to make a perfectly informed choice for your special project.

Then we need a special quote button which takes them directly to our email link. On this page we also need to add: We have had 25 years' experience printing books saving customers time and money whilst guaranteeing quality

Page 6: Logo repeated from page one with name: Morgan Elsworth and mobile phone no 0487 552 314

- Must follow the brief exactly. Must have a turn page book. Clear, simple and concise with a touch of creative flare and must lead into a call for action which is there quotation. A unique button for quotation link...something out of the ordinary which makes someone want to get a quote.

- It would be nice to have 3D Logo on Page 1 & 6.
a unique button for quotation link...something that make someone eager to proceed.

Our main objective is that they should not leave our website without giving us a quote. Please make sure that the spelling is correct and we do not require clip art images. Continue the logo colours through the theme
Updates

here is another example www.vidharbor.example/watch?v=JbXo412TrGe Added Saturday, May 13, 2017

Target Market(s)

Schools, Universities, Self Publishers, Publishers, Graphic Designers, Conference Providers, Businesses, Corporations, Government.

Industry/Entity Type

Printing

Coding

Coded - Design and coding required

Number of Pages Required

5+ page

Font styles to use
Sans Serif

Colors
34a6d7
ec1f27
fbed22
9bcb3c
ffc214
6b449b

Requirements
Must have
• Must follow the brief exactly. Must have a turn page book. Clear, simple and concise with a touch of creative flare and must lead into a call for action which is there quotation. A unique button for quotation link...something out of the ordinary which makes someone want to get a quote. would like to see the colours of the logo use throughout
Nice to have
• 3D Logo on Page 1 & 6.
• a unique button for quotation link...something that make someone eager to proceed.
• Our main objective is that they should not leave our website without giving us a quote
Should not have
• Spelling mistakes, clip art, ordinary design

```html
<!DOCTYPE html>
<html lang="en">
<head>
<meta charset="utf-8">
<title>Quill Press Oceania — Black and White Book</title>
<link rel="stylesheet" href="https://fonts.googleapis.com/css2?family=Roboto+Condensed:wght@400;700&display=swap">
<style>
  :root {
    --page-bg: #121316;
    --photo-deep: #0d0e11;
    --photo-mid: #1d1f25;
    --ink-yellow: #fbed22;
    --ink-magenta: #c2187a;
    --ink-cyan: #34a6d7;
    --text-main: #ffffff;
    --text-soft: #e6e6e6;
    --folio: #b9b9b9;
  }
  * { box-sizing: border-box; margin: 0; padding: 0; }
  html, body {
    width: 720px;
    height: 1200px;
    overflow: hidden;
    background: var(--page-bg);
  }
  .book-page {
    position: relative;
    width: 720px;
    height: 1200px;
    overflow: hidden;
    font-family: "Roboto Condensed", "Arial Narrow", sans-serif;
    color: var(--text-main);
  }
  .press-photo {
    position: absolute;
    inset: 0;
    background:
      radial-gradient(ellipse 140px 190px at 100px 230px, rgba(251,237,34,0.16), transparent 70%),
      radial-gradient(ellipse 110px 170px at 330px 190px, rgba(194,24,122,0.16), transparent 70%),
      radial-gradient(ellipse 100px 160px at 500px 170px, rgba(52,166,215,0.14), transparent 70%),
      radial-gradient(ellipse 140px 190px at 110px 1000px, rgba(251,237,34,0.16), transparent 70%),
      radial-gradient(ellipse 110px 170px at 330px 1040px, rgba(194,24,122,0.16), transparent 70%),
      radial-gradient(ellipse 100px 160px at 500px 1050px, rgba(52,166,215,0.14), transparent 70%),
      radial-gradient(ellipse 420px 520px at 360px 620px, var(--photo-deep), var(--photo-mid));
  }
  .page-content {
    position: absolute;
    left: 0;
    right: 0;
    top: 452px;
    text-align: center;
  }
  .brand-name {
    display: block;
    font-weight: 700;
    font-size: 44px;
    line-height: 1;
    letter-spacing: 0.5px;
    color: var(--text-main);
    margin-bottom: 104px;
  }
  .page-title {
    font-weight: 700;
    font-size: 41px;
    line-height: 1;
    letter-spacing: 0.3px;
    text-transform: uppercase;
    margin-bottom: 34px;
  }
  .page-text {
    font-weight: 400;
    font-size: 29px;
    line-height: 38px;
    color: var(--text-soft);
  }
  .folio {
    position: absolute;
    right: 20px;
    bottom: 32px;
    font-size: 15px;
    color: var(--folio);
  }
</style>
</head>
<body>
  <main class="book-page">
    <div class="press-photo" role="img" aria-label="Dark close-up photograph of a printing press with yellow, magenta and cyan ink cartridges labelled push"></div>
    <section class="page-content">
      <span class="brand-name">Quill Press Oceania</span>
      <h1 class="page-title">Black and White Book</h1>
      <p class="page-text">These are produced either<br>digitally or offset on a complete<br>range of stocks</p>
    </section>
    <span class="folio">C7</span>
  </main>
</body>
</html>
```